Wordpress Web Design & Coding for velcorahealth.ca

We need a website for a new investment company that is visually grabbing and vibrant. We would like to see a web page that displays trust, growth and confidence. Needs to be responsive and mobile friendly for all browsers and coded for both Android & IOS.

Open to the number of pages and menu items. I selected 4 but if you feel the layout would work better with less I am open to this. Need to sell the people (management team/related businesses) and then show where the invested money will be going (upcoming projects).

Company Info:

Vel Cora is an investment company put together by a group of seasoned business professionals who have come together to combine decades of success in the real estate development, management, financing and medical services. The company will be a full service company offering turn key solutions for medical professionals.

Vel-Cora will focus on providing a full range of services via a group of distinct companies to deliver newly emerging needs of the medical community. The end goal will be to create complete solutions for individuals in the medical community. Our group has experience and success with the conceptualization, construction and financing of medical and dental clinic spaces. Vel-Cora Solutions will be established to accommodate all areas of the development and creation of clinics for medical professionals from building construction to equipment financing and administrations.

You can mention these companies and take photos from their websites. You can also use stock photos.

Our construction partner:
https://318bld.com/projects/

Our equipment leasing partner:
https://www.norvixa.com/

Our Management Team and medical partners

Gil Parish
https://www.ourfirmstance.ca/

Dietmar Vellasquin
https://www.gshdentalservices.com/about-us

PROPOSED PROJECTS (see attachment for details)
Pinegrove Business Park
Holtmere Business Park
Mt. Corwin Ridge Professional

Target Market(s)

Investors

Industry/Entity Type

Investment

Coding

Coded - Design and coding required

Number of Pages Required

4 page

Font styles to use
Sans Serif

Requirements
Must have
• Wordpress – must be both desktop and mobile friendly with fast page load speed
Ability to edit after ourselves in Wordpress
Attractive home page with logo etc.
Logo colours are: for the blue the pantone color is #0355a3
and for the green is #8cc63f

Sections, about us, what we do/services we provide, contact us

```html
<!DOCTYPE html>
<html lang="en">
<head>
<meta charset="utf-8">
<title>Vel-Cora Solutions</title>
<link rel="stylesheet" href="https://fonts.googleapis.com/css2?family=Montserrat:wght@400;500;600;700&display=swap">
<style>
:root{
  --blue:#0355a3;
  --blue-deep:#0a4c98;
  --green:#8cc63f;
  --ink:#1d1d1f;
  --muted:#7a7a7a;
  --line:#ececec;
  --card:#f2f2f2;
  --white:#ffffff;
}
*{margin:0;padding:0;box-sizing:border-box}
html,body{width:1200px;height:4360px;overflow:hidden}
body{position:relative;font-family:"Montserrat",Arial,sans-serif;color:var(--ink);background:var(--white)}
.abs{position:absolute}
.hero{left:0;top:0;width:1200px;height:790px;background:linear-gradient(100deg,#3b3e42 0%,#4a4e53 40%,#2f4f78 70%,#1f3a60 100%)}
.hero-shade{left:0;top:0;width:1200px;height:790px;background:rgba(20,24,30,.35)}
.nav{left:215px;top:25px;width:769px;height:51px;background:var(--white);display:flex;align-items:center;padding:0 22px}
.brand{display:flex;align-items:center;gap:8px;font-weight:700;font-size:17px;color:var(--blue);letter-spacing:.3px}
.brand-mark{width:18px;height:18px;background:var(--green)}
.menu{display:flex;gap:24px;margin-left:34px;font-size:11px;color:var(--ink)}
.menu .active{color:var(--blue)}
.lang{margin-left:auto;font-size:10px;font-weight:600}
.lang span{color:#c8c8c8;font-weight:400}
.hero-title{left:0;top:236px;width:1200px;text-align:center;color:var(--white);font-weight:700;font-size:37px;line-height:45px}
.btn{left:537px;top:418px;width:125px;height:39px;background:var(--green);color:var(--white);font-size:11px;font-weight:700;display:flex;align-items:center;justify-content:center}
.contact-row{top:590px;font-size:11px;color:var(--white)}
.contact-row b{color:var(--green);font-weight:600;font-size:12px}
.social{display:flex;gap:14px;align-items:center}
.dot{width:9px;height:9px;border-radius:50%;background:var(--white)}
.dot.g{background:var(--green)}
.why{left:207px;top:632px;width:787px;height:474px;background:var(--blue);box-shadow:0 20px 40px rgba(0,0,0,.12)}
.eyebrow{font-size:9px;font-weight:700;letter-spacing:.2px;text-transform:uppercase}
.why .eyebrow{position:absolute;left:0;width:100%;text-align:center;top:84px;color:var(--white)}
.why-lead{left:60px;top:152px;width:324px;text-align:right;color:var(--white);font-weight:600;font-size:22px;line-height:30px}
.why-item{left:447px;width:270px}
.why-item h3{color:var(--green);font-size:14px;font-weight:600;margin-bottom:10px}
.why-item p{color:#c9d9ee;font-size:9px;line-height:15px}
.vline{top:1106px;width:1px;height:2747px;background:var(--line)}
.vline.lower{top:3130px;height:723px}
.section-label{left:0;width:1200px;text-align:center}
.ph{background:linear-gradient(135deg,#cfd6dc,#8fa0ae)}
.proj-title{color:var(--green);font-size:14px;font-weight:600;line-height:15px}
.proj-title.dark{color:var(--ink)}
.proj-text{font-size:9px;line-height:15px;color:var(--muted)}
.learn{font-size:9px;color:var(--green)}
.bar-v{width:2px;background:var(--green)}
.bar-h{height:2px;background:var(--green)}
.band{left:0;top:2538px;width:1200px;height:592px;background:linear-gradient(180deg,#1f5aa8 0%,#2a63ad 50%,#1a55a2 100%)}
.band-small{left:0;top:2592px;width:1200px;text-align:center;color:var(--white);font-size:9px;line-height:16px}
.band-quote{left:0;top:2768px;width:1200px;text-align:center;color:var(--white);font-weight:700;font-size:24px;line-height:37.5px}
.card{height:168px;background:var(--card);display:flex}
.card .img{width:125px;height:168px;flex:none}
.card .body{padding:14px 16px}
.card .role{font-size:9px;color:var(--muted);margin-bottom:6px}
.card h4{font-size:12px;font-weight:700;margin-bottom:10px}
.card h4.g{color:#f0a020}
.card p{font-size:8.5px;line-height:15px;color:var(--muted);height:60px;overflow:hidden}
.card a{display:inline-block;margin-top:12px;font-size:9px;color:var(--ink);text-decoration:underline}
.foot{left:0;top:3853px;width:1200px;height:507px;background:var(--green);text-align:center;color:var(--ink)}
.foot .eyebrow{position:absolute;left:0;width:100%;top:121px}
.foot-mail{position:absolute;left:0;width:100%;top:150px;font-size:37px;font-weight:700}
.foot-addr{position:absolute;left:0;width:100%;top:203px;font-size:14px;font-weight:600;line-height:27px}
.foot-links{position:absolute;left:0;width:100%;top:311px;font-size:10px;display:flex;justify-content:center;gap:22px}
.foot-copy{position:absolute;left:0;width:100%;top:341px;font-size:9px}
.foot .brand{position:absolute;left:0;width:100%;top:409px;justify-content:center;font-size:13px;color:var(--blue)}
.foot .brand-mark{width:14px;height:14px;background:var(--blue)}
</style>
</head>
<body>

<div class="abs hero" role="img" aria-label="Photo of a doctor at a bright clinic reception desk with shelves and blinds"></div>
<div class="abs hero-shade"></div>

<nav class="abs nav">
  <div class="brand"><span class="brand-mark"></span>VEL-CORA SOLUTIONS</div>
  <div class="menu"><span class="active">Home</span><span>About Us</span><span>What we do</span><span>Solutions</span><span>Contact us</span></div>
  <div class="lang">ENG <span>/ FRA</span></div>
</nav>

<h1 class="abs hero-title">To assist the medical<br>community in catering<br>to those services</h1>
<div class="abs btn">ENQUIRE NOW!</div>

<div class="abs contact-row" style="left:235px">Email: hello@vel-cora.com</div>
<div class="abs contact-row" style="left:410px">Phone: <b>(+012) 555-0142-77</b></div>
<div class="abs contact-row social" style="left:775px">Follow us: <span class="dot g"></span><span class="dot"></span><span class="dot"></span><span class="dot"></span><span class="dot"></span></div>

<section class="abs why">
  <div class="eyebrow">Why choose Vel-Cora</div>
  <p class="abs why-lead">We are a group of seasoned business professionals who have come together to combine decades of success in the real estate development.</p>
  <div class="abs why-item" style="top:155px"><h3>Professional Liability</h3><p>Donec lacinia mi rutrum sagittis consequat. Donec sagittis, tellus sodales sollicitudin commodo</p></div>
  <div class="abs why-item" style="top:243px"><h3>Dedicated To Our Clients</h3><p>Quisque mollis metus magna, ut accumsan elit hendrerit ac. Lorem ipsum dolor sit amet,</p></div>
  <div class="abs why-item" style="top:331px"><h3>Outstanding Services</h3><p>lacinia mi rutrum sagittis consequat. Donec sagittis, tellus sodales sollicitudin commodo, risus urna interdum massa</p></div>
</section>

<div class="abs vline" style="left:234px"></div>
<div class="abs vline" style="left:723px;height:1432px"></div>
<div class="abs vline lower" style="left:723px"></div>
<div class="abs vline" style="left:965px"></div>

<div class="abs section-label eyebrow" style="top:1183px">Proposed projects</div>

<div class="abs ph" style="left:359px;top:1258px;width:364px;height:235px" role="img" aria-label="Photo of two doctors reviewing a tablet in a glass atrium"></div>
<div class="abs bar-v" style="left:963px;top:1258px;height:79px"></div>
<div class="abs" style="left:777px;top:1258px;width:140px">
  <div class="proj-title">Pinegrove<br>Business Park</div>
  <p class="proj-text" style="margin-top:18px">The Pinegrove Business Park in Pinegrove, British Columbia on Vancouver island, is presently under contract with partners that are controlled by individuals who form part of the Vel-Cora management group. The purchase of the land will be closing early summer 2020.</p>
  <p class="learn" style="margin-top:20px">Learn More</p>
</div>

<div class="abs bar-h" style="left:234px;top:1582px;width:83px"></div>
<svg class="abs" style="left:240px;top:1624px" width="22" height="22" viewBox="0 0 22 22"><circle cx="11" cy="11" r="6" fill="none" stroke="#dcdcdc"/><path d="M11 0v22M0 11h22" stroke="#dcdcdc"/></svg>
<div class="abs" style="left:359px;top:1582px;width:130px">
  <div class="proj-title">Holtmere<br>Business Park</div>
  <p class="proj-text" style="margin-top:18px">The city of Holtmere is a core municipality in the Western Communities. It is currently experiencing regional increases in population driven by residential, commercial and industrial development. Holtmere projected an increase in its population of 12.5% by 2026. The 2016 census indicated that Holtmere ranked number one in growth among</p>
  <p class="learn" style="margin-top:18px">Learn More</p>
</div>
<div class="abs" style="left:547px;top:1583px;width:418px;height:286px;background:linear-gradient(180deg,#1f4fb0,#2a5bbd)" role="img" aria-label="Blueprint site plan of the business park"></div>

<div class="abs ph" style="left:234px;top:1960px;width:245px;height:387px;background:linear-gradient(180deg,#c9cdd1,#8e959c)" role="img" aria-label="Photo of a glazed walkway bridge between buildings"></div>
<div class="abs bar-v" style="left:589px;top:1960px;height:80px"></div>
<div class="abs" style="left:654px;top:1960px;width:312px">
  <div class="proj-title dark">Mt. Corwin Ridge Professional</div>
  <p class="proj-text" style="margin-top:18px">Mt. Corwin Ridge Professional building will feature a repurposed building adjacent to Mt. Corwin Trail in Mt. Corwin, AB. This location served as a car dealership, but will be renovated from its current structure to a two storey building to house professional and medical services. The high profile location fronting the trail sees more than 45,000 vehicles per day making it the ideal high profile location for Vel-Cora.</p>
  <p class="learn" style="margin-top:22px">Learn More</p>
</div>
<svg class="abs" style="left:580px;top:2246px" width="22" height="22" viewBox="0 0 22 22"><circle cx="11" cy="11" r="6" fill="none" stroke="#dcdcdc"/><path d="M11 0v22M0 11h22" stroke="#dcdcdc"/></svg>
<div class="abs eyebrow" style="left:654px;top:2244px;text-decoration:underline">Pricing / Plans / Packages</div>

<div class="abs section-label eyebrow" style="top:2453px">Security</div>

<div class="abs band" role="img" aria-label="Blue tinted photo of a commercial building with tenant signage"></div>
<p class="abs band-small">Vel-Cora Solutions' leasing division will implement a number of security measures which ensures investors<br>are secure and returns are maximized over the life of the investments.</p>
<p class="abs band-quote">As we embark on this newest chapter, our<br>combined knowledge will build on the<br>discussions of the privatization in medical<br>services that are ongoing at this time. One of our<br>strategic goals is to assist the medical community<br>in catering to those services.</p>

<div class="abs eyebrow" style="left:234px;top:3215px">Partners</div>
<div class="abs" style="left:880px;top:3215px;font-size:9px;color:var(--muted)">See all partners</div>

<div class="abs card" style="left:234px;top:3279px;width:357px">
  <div class="img" style="background:linear-gradient(180deg,#7fa4cf,#dfe3e6)" role="img" aria-label="Photo of a modern office building"></div>
  <div class="body"><div class="role">Construction Partner</div><h4 class="g">318 BUILDERS INC.</h4><p>318 Builders has a broad range of experience providing design, construction services and interior improvements for commercial office and warehouse buildings</p><a>Learn More</a></div>
</div>
<div class="abs card" style="left:609px;top:3279px;width:356px">
  <div class="img" style="background:linear-gradient(160deg,#f4f1ea,#d8d2c4)" role="img" aria-label="Photo of dental equipment"></div>
  <div class="body"><div class="role">Equipment Leasing Partner</div><h4>Norvixa Equipment Leasing Inc.</h4><p>Small business owners need fast answers. We pride ourselves on being customer focused and responsive to your needs. You can expect</p><a>Learn More</a></div>
</div>

<div class="abs eyebrow" style="left:234px;top:3512px">Management team and medical partners</div>

<div class="abs card" style="left:234px;top:3574px;width:357px">
  <div class="img" style="background:linear-gradient(180deg,#8b8f94,#4b4f55)" role="img" aria-label="Portrait photo of Dr. Gil Parish"></div>
  <div class="body"><div class="role">Medical Partner</div><h4>Dr. Gil Parish</h4><p>A published author and experienced, board-certified physician in the field of Bioidentical Hormone Replacement Therapy. Dr. Parish believes in a holistic approach to</p><a>Learn More</a></div>
</div>
<div class="abs card" style="left:609px;top:3574px;width:356px">
  <div class="img" style="background:linear-gradient(180deg,#9cc3e6,#5f7d99)" role="img" aria-label="Portrait photo of Dietmar Vellasquin"></div>
  <div class="body"><div class="role">Equipment Leasing Partner</div><h4>Dietmar Vellasquin</h4><p>Dietmar brings more than 25 years of experience working with dentists across Western Canada as an equipment specialist and a</p><a>Learn More</a></div>
</div>

<footer class="abs foot">
  <div class="eyebrow">Let's work together</div>
  <div class="foot-mail">hello@vel-cora.com</div>
  <div class="foot-addr">48 Halden Row, 9th Floor . Corwin, Alberta, Canada<br>(+012) 555-0198-31</div>
  <div class="foot-links"><span>Updates</span><span style="text-decoration:underline">Community</span><span>Portfolio</span><span>Gallery</span></div>
  <div class="foot-copy">© 2020 Vel-Cora. All Right Reserved</div>
  <div class="brand"><span class="brand-mark"></span>VEL-CORA SOLUTIONS</div>
</footer>

</body>
</html>
```